Create a highly polished design and structured Sales Agreement template

We need a professionally designed Sales Agreement template for our company, Harrowgate Labs, Inc. This template will be used to formalize agreements with our customers for calibration services. The design should reflect the high standards and professionalism of a Keystone 250 company.
Key requirements:
Incorporate our company logo and branding elements.
Ensure the template includes sections for all critical details such as customer name, address, services provided, pricing, and terms of payment.
The layout should be clean, modern, and easy to navigate.
Include placeholders for variable information (e.g., customer name, address, etc.) that can be easily filled out for each customer.
Design the template in a way that allows our team to update it easily via a form entry system.
Ensure the language and formatting are polished and professional.
We have attached our current Sales Agreement for reference. Please maintain all key details while enhancing the structure, format, and overall presentation.

```html
<!DOCTYPE html>
<html lang="en">
<head>
<meta charset="utf-8">
<title>Harrowgate Labs – Facilities Management Service Proposal</title>
<link href="https://fonts.googleapis.com/css2?family=Montserrat:wght@400;500;600;700&family=Oswald:wght@600;700&display=swap" rel="stylesheet">
<style>
:root{
  --stage:#3a3a3c;
  --paper:#ffffff;
  --teal:#13968a;
  --ink:#1c1c1c;
  --text:#333333;
  --grey:#c8c8c8;
  --grey-light:#e6e6e6;
  --grey-mid:#d2d2d2;
}
*{box-sizing:border-box;margin:0;padding:0}
html,body{width:1200px;height:1076px;overflow:hidden;background:var(--stage)}
body{position:relative;font-family:"Montserrat",sans-serif;color:var(--text)}
.page{position:absolute;width:313px;height:443px;background:var(--paper);overflow:hidden;box-shadow:0 2px 6px rgba(0,0,0,.35)}
.p1{left:100px;top:70px}.p2{left:441px;top:70px}.p3{left:786px;top:70px}
.p4{left:100px;top:547px}.p5{left:441px;top:547px}.p6{left:786px;top:547px}

.top-band{position:absolute;left:0;top:0;width:293px;height:7px;background:var(--grey);border-bottom-right-radius:7px}
.footer{position:absolute;left:0;right:0;bottom:0;height:15px;background:var(--teal);color:#fff;font-size:5.6px;font-weight:600;letter-spacing:.2px;display:flex;justify-content:space-between;align-items:center;padding:0 17px}
.footer::before{content:"";position:absolute;left:56%;right:0;top:-3px;height:3px;background:var(--grey-light);border-top-left-radius:4px}

.page-title{position:absolute;left:18px;top:28px;line-height:1}
.page-title .line1{display:block;font-size:11.5px;font-weight:700;color:var(--ink)}
.page-title .line2{display:block;font-size:15px;font-weight:700;color:var(--teal);margin-top:1px}

.brand{position:absolute;right:22px;top:36px;display:flex;align-items:center;gap:3px}
.brand .dot{width:9px;height:9px;border-radius:50%;background:var(--grey-mid);flex:none}
.brand .name{font-size:5.4px;font-weight:700;color:var(--teal);text-transform:uppercase;white-space:nowrap}

.body{position:absolute;left:18px;right:17px;top:77px}
.body p,.col p{font-size:4.5px;line-height:7.6px;text-align:justify}
.h-teal{font-size:8px;font-weight:600;color:var(--teal);letter-spacing:.2px;margin-bottom:2px}
.h-dark{font-size:8.8px;font-weight:600;color:var(--ink);letter-spacing:.2px;margin-bottom:2px}
.h-sub{font-size:7.2px;font-weight:600;color:var(--ink)}

/* Cover */
.cover-strip{position:absolute;left:0;top:0;bottom:0;width:12px;background:linear-gradient(90deg,#d9d9d9,#f1f1f1)}
.cover-fade{position:absolute;left:12px;top:0;bottom:0;width:160px;background:linear-gradient(90deg,#e9e9e9,rgba(255,255,255,0))}
.cover-art{position:absolute;inset:0}
.cover-brand{position:absolute;left:29px;top:42px;display:flex;align-items:center;gap:5px}
.cover-brand .dot{width:16px;height:16px;border-radius:50%;background:var(--grey-mid);flex:none}
.cover-brand .name{font-size:9px;font-weight:700;color:var(--teal);text-transform:uppercase;white-space:nowrap}
.cover-title{position:absolute;left:29px;top:102px;font-family:"Oswald",sans-serif;font-weight:700;font-size:38px;line-height:41px;color:var(--ink)}
.cover-title .accent{color:var(--teal)}
.cover-sub{position:absolute;left:29px;top:359px;font-size:17px;font-weight:700;line-height:19px;color:var(--ink)}
.cover-sub .accent{color:var(--teal)}
.cover-url{position:absolute;left:29px;top:419px;font-size:6.6px;letter-spacing:.6px;color:var(--ink)}

/* TOC */
.toc{position:absolute;left:20px;right:27px;top:87px}
.toc-group{position:relative;padding-left:10px;margin-bottom:21px}
.toc-group::before{content:"";position:absolute;left:2px;top:4px;width:5px;height:5px;border:1px dashed var(--teal);border-radius:50%}
.toc-row{display:flex;align-items:baseline;font-size:5.8px;line-height:9.5px;color:var(--ink)}
.toc-row.title{color:var(--teal);font-weight:700}
.toc-row .label{width:74px}
.toc-row .leader{flex:1;border-bottom:.5px dotted #777;margin:0 4px}
.toc-line{position:absolute;left:24px;top:97px;height:235px;border-left:.6px dashed var(--teal)}
.toc-art{position:absolute;left:10px;top:272px;width:96px;height:146px;border-radius:6px;background:linear-gradient(160deg,#dcdedf,#c4c8ca 55%,#e4e6e6)}

/* Agreement */
.agreement .h-teal{margin-top:9px}
.agreement .h-teal:first-child{margin-top:0}
.agreement p{font-size:4.5px;line-height:7.6px;text-align:left}
.agreement ol{list-style:none;font-size:4.5px;line-height:7.6px}
.agreement ol li span{color:var(--teal);font-weight:600}
.agreement .strong{font-weight:700;color:var(--ink)}
.agreement .sig-label{font-size:4.8px;font-weight:600;color:var(--teal);margin-top:17px}
.agreement .sig-block{margin-top:31px}
.agreement .sig-block2{margin-top:8px}

/* Chart & table */
.chart{position:absolute;left:152px;top:161px;width:136px;height:82px}
.bullets{font-size:4.5px;line-height:8.7px;padding-left:19px;color:var(--text)}
.data-table{position:absolute;left:16px;top:322px;width:281px;border-collapse:collapse;font-size:4.2px;color:var(--text)}
.data-table th{background:var(--grey);color:#fff;font-weight:500;height:14px;line-height:5px;text-align:center}
.data-table th:first-child{text-align:left;padding-left:3px}
.data-table th.active{background:var(--teal)}
.data-table td{height:12.6px;border-bottom:.6px solid #cfcfcf;text-align:center}
.data-table td:first-child{text-align:left;padding-left:3px}
.data-table td.active{border-left:.8px solid var(--teal);border-right:.8px solid var(--teal)}
.data-table tr:last-child td.active{border-bottom:.8px solid var(--teal)}

/* Columns */
.col{position:absolute;width:126px}
.photo{position:absolute}
</style>
</head>
<body>

<!-- Cover -->
<section class="page p1">
  <div class="cover-strip"></div>
  <div class="cover-fade"></div>
  <svg class="cover-art" viewBox="0 0 313 443" role="img" aria-label="Photograph of a bright modern cleanroom facility with machinery">
    <defs>
      <linearGradient id="facility" x1="0" y1="0" x2="0" y2="1">
        <stop offset="0" stop-color="#aebfc9"/>
        <stop offset=".55" stop-color="#d6e2e8"/>
        <stop offset="1" stop-color="#eef3f5"/>
      </linearGradient>
    </defs>
    <path d="M240 0 C215 55 238 110 212 175 C195 220 165 245 140 270 C118 300 112 352 128 372 C168 405 262 405 313 402 L313 0 Z" fill="url(#facility)"/>
    <path d="M212 175 C195 220 165 245 140 270 C125 288 117 310 116 330" fill="none" stroke="var(--teal)" stroke-width="2"/>
  </svg>
  <div class="cover-brand"><span class="dot"></span><span class="name">Harrowgate Labs</span></div>
  <h1 class="cover-title">FACILITIES<br><span class="accent">MANAGEMENT</span><br>SERVICE</h1>
  <div class="cover-sub">COMPANY<br><span class="accent">PROPOSAL</span><br><span class="accent">2024</span></div>
  <div class="cover-url">www.harrowgatelabs.com</div>
</section>

<!-- Table of contents -->
<section class="page p2">
  <div class="top-band"></div>
  <h2 class="page-title"><span class="line1">TABLE OF</span><span class="line2">CONTENTS</span></h2>
  <div class="brand"><span class="dot"></span><span class="name">Harrowgate Labs</span></div>
  <div class="toc-line"></div>
  <div class="toc">
    <div class="toc-group">
      <div class="toc-row title"><span class="label">1. TITLE GOES HERE</span><span class="leader"></span><span>1</span></div>
      <div class="toc-row"><span class="label">1.1 Heading Goes Here</span><span class="leader"></span><span>1</span></div>
      <div class="toc-row"><span class="label">1.2 Heading Goes Here</span><span class="leader"></span><span>2</span></div>
    </div>
    <div class="toc-group">
      <div class="toc-row title"><span class="label">2. TITLE GOES HERE</span><span class="leader"></span><span>4</span></div>
      <div class="toc-row"><span class="label">1.1 Heading Goes Here</span><span class="leader"></span><span>4</span></div>
      <div class="toc-row"><span class="label">1.2 Heading Goes Here</span><span class="leader"></span><span>5</span></div>
    </div>
    <div class="toc-group">
      <div class="toc-row title"><span class="label">3. TITLE GOES HERE</span><span class="leader"></span><span>7</span></div>
      <div class="toc-row"><span class="label">1.1 Heading Goes Here</span><span class="leader"></span><span>7</span></div>
      <div class="toc-row"><span class="label">1.2 Heading Goes Here</span><span class="leader"></span><span>8</span></div>
    </div>
    <div class="toc-group">
      <div class="toc-row title"><span class="label">4. TITLE GOES HERE</span><span class="leader"></span><span>10</span></div>
      <div class="toc-row"><span class="label">1.1 Heading Goes Here</span><span class="leader"></span><span>10</span></div>
      <div class="toc-row"><span class="label">1.2 Heading Goes Here</span><span class="leader"></span><span>12</span></div>
    </div>
  </div>
  <div class="toc-art" role="img" aria-label="Decorative cluster of grey and teal gears"></div>
  <footer class="footer"><span>FACILITIES MANAGEMENT SERVICE</span><span>COMPANY PROPOSAL 2024</span></footer>
</section>

<!-- Sales agreement -->
<section class="page p3">
  <div class="top-band"></div>
  <h2 class="page-title"><span class="line1">SALES</span><span class="line2">AGREEMENT</span></h2>
  <div class="brand"><span class="dot"></span><span class="name">Harrowgate Labs</span></div>
  <div class="body agreement" style="top:73px">
    <h3 class="h-teal">Seller:</h3>
    <p>Harrowgate Labs, Inc. 410 Meridian Way, Suite B Fairview, OR 97024 Phone: 800-555-0142</p>
    <h3 class="h-teal">Customer:</h3>
    <p>[Customer Name] [Customer Address] [Customer City, State, Zip] Phone: [Customer Phone] Email: [Customer Email]</p>
    <h3 class="h-teal" style="margin-top:12px">SERVICES</h3>
    <p>Harrowgate Labs, Inc. agrees to provide the following services to [Customer Name]:</p>
    <ol>
      <li><span>1.</span> Calibration Services: Full-time on-site trained technician support.</li>
      <li><span>2.</span> Turn-key Service Management: Scheduling, on-site calibrations, pick-up and delivery, turn time management, and<br>&nbsp;&nbsp;&nbsp;interface with selected vendors.</li>
      <li><span>3.</span> Document Control: Online access to calibration documents via our website.</li>
    </ol>
    <h3 class="h-teal" style="margin-top:10px">PRICING</h3>
    <p class="strong">Dedicated On-site Technician (3 Days per Week)</p>
    <p>· Monthly Charge: $12,500.00<br>· Yearly Total: $150,000.00<br>· Sales tax not included.<br>· Potential annual price increase of 3% beginning the second year.</p>
    <div class="sig-label">SIGNATURES</div>
    <p class="strong">Harrowgate Labs, Inc.:</p>
    <p class="sig-block">[Authorized Signatory Name]<br>[Title]<br>Date: ____________<br>[Customer Name]:</p>
    <p class="sig-block2">[Authorized Signatory Name]<br>[Title]<br>Date: ____________</p>
  </div>
  <footer class="footer"><span>FACILITIES MANAGEMENT SERVICE</span><span>COMPANY PROPOSAL 2024</span></footer>
</section>

<!-- Content page with chart and table -->
<section class="page p4">
  <div class="top-band"></div>
  <h2 class="page-title"><span class="line1">HEADING</span><span class="line2">GOES HERE</span></h2>
  <div class="brand"><span class="dot"></span><span class="name">Harrowgate Labs</span></div>
  <div class="body" style="left:17px;top:71px">
    <h3 class="h-teal">HEADING GOES HERE</h3>
    <p>Lorem ipsum dolor sit amet, consectetuer adipiscing elit, sed diam nonummy nibh euismod tincidunt ut laoreet dolore magna aliquam erat volutpat. Ut wisi enim ad minim veniam, quis nostrud exerci tation ullamcorper suscipit lobortis nisl ut aliquip ex ea commodo consequat. Duis autem vel eum iriure dolor in hendrerit in vulputate velit esse molestie consequat, vel illum dolore eu feugiat nulla facilisis at vero eros et accumsan et iusto odio dignis Lorem ipsum dolor sit amet, consectetuer adipiscing elit, sed diam nonummy nibh euismod tincidunt ut laoreet dolore magna aliquam erat volutpat. Ut wisi enim ad minim veniam, quis nostrud exerci tation ullamcorper suscipit lobortis nisl ut aliquip ex ea tation ullamcorper suscipit lobortis nisl ut aliquip ex ea commodo consequat. Duis autem vel eum iriure dolor in hendrerit in vulputate velit esse molestie consequat, vel illum dolore eu feugiat nulla facilisis at vero eros et accumsan et iusto odio dignis</p>
    <h4 class="h-sub" style="margin-top:6px">1.1. HEADING GOES HERE</h4>
    <div class="bullets">a) Lorem ipsum dolor sit amet,<br>b)Lorem ipsum dolor sit amet,</div>
    <h4 class="h-sub" style="margin-top:7px">1.2. HEADING GOES HERE</h4>
    <div class="bullets" style="margin-top:3px">a) Lorem ipsum dolor sit amet,<br>b) Lorem ipsum dolor sit amet,<br>c) Lorem ipsum dolor sit amet,<br>d) Lorem ipsum dolor sit amet,</div>
    <h3 class="h-teal" style="margin-top:15px">HEADING GOES HERE</h3>
    <p>Lorem ipsum dolor sit amet, consectetuer adipiscing elit, sed diam nonummy nibh euismod tincidunt ut laoreet dolore magna aliquam erat volutpat. Ut wisi enim ad minim veniam, quis nostrud exerci tation ullamcorper suscipit lobortis nisl ut aliquip ex ea tation ullamcorper suscipit lobortis nisl ut aliquip ex ea commodo consequat. Duis autem vel eum iriure dolor in hendrerit in vulputate velit esse molestie consequat, vel illum dolore eu feugiat nulla facilisis at vero eros et accumsan et iusto odio dignis Lorem ipsum dolor sit amet,</p>
  </div>
  <svg class="chart" viewBox="0 0 136 82" font-family="Montserrat, sans-serif">
    <text x="20" y="7" font-size="7" fill="#555" font-weight="500">Temperature in well 20 in °C</text>
    <g font-size="3.6" fill="#777" text-anchor="end">
      <text x="8" y="19">140</text><text x="8" y="26">120</text><text x="8" y="33">100</text><text x="8" y="40">80</text>
      <text x="8" y="47">60</text><text x="8" y="54">40</text><text x="8" y="61">20</text><text x="8" y="68">0</text>
    </g>
    <line x1="11" y1="67" x2="132" y2="67" stroke="#bbb" stroke-width=".4"/>
    <g fill="#c9c9c9">
      <rect x="13" y="47.4" width="8" height="19.6"/>
      <rect x="26" y="52.3" width="8" height="14.7"/>
      <rect x="39" y="36.9" width="8" height="30.1"/>
      <rect x="52" y="35.5" width="8" height="31.5"/>
      <rect x="65" y="32.7" width="8" height="34.3"/>
      <rect x="78" y="26.8" width="8" height="40.2"/>
      <rect x="91" y="23.3" width="8" height="43.7"/>
      <rect x="104" y="22.6" width="8" height="44.4"/>
      <rect x="117" y="21.9" width="8" height="45.1"/>
    </g>
    <g font-size="3.6" fill="#666" text-anchor="middle">
      <text x="17" y="46">56</text><text x="30" y="51">42</text><text x="43" y="35.5">86</text><text x="56" y="34">90</text>
      <text x="69" y="31.3">98</text><text x="82" y="25.4">115</text><text x="95" y="21.9">125</text><text x="108" y="21.2">127</text><text x="121" y="20.5">129</text>
      <text x="17" y="74">2000</text><text x="30" y="74">2002</text><text x="43" y="74">2003</text><text x="56" y="74">2004</text><text x="69" y="74">2005</text>
      <text x="82" y="74">2006</text><text x="95" y="74">2007</text><text x="108" y="74">2008</text><text x="121" y="74">2009</text>
    </g>
  </svg>
  <table class="data-table">
    <tr><th>Heading Goes Here</th><th class="active">Heading<br>Goes Here</th><th>Heading<br>Goes Here</th><th>Heading<br>Goes Here</th><th>Heading<br>Goes Here</th></tr>
    <tr><td>Lorem Ipsum Goes Here</td><td class="active">23</td><td>12</td><td>78</td><td>12</td></tr>
    <tr><td>Lorem Ipsum Goes Here</td><td class="active">45</td><td>56</td><td>12</td><td>56</td></tr>
    <tr><td>Lorem Ipsum Goes Here</td><td class="active">78</td><td>76</td><td>34</td><td>76</td></tr>
    <tr><td>Lorem Ipsum Goes Here</td><td class="active">22</td><td>12</td><td>55</td><td>12</td></tr>
  </table>
  <footer class="footer"><span>FACILITIES MANAGEMENT SERVICE</span><span>COMPANY PROPOSAL 2024</span></footer>
</section>

<!-- Two-column page -->
<section class="page p5">
  <div class="top-band"></div>
  <h2 class="page-title"><span class="line1">HEADING</span><span class="line2">GOES HERE</span></h2>
  <div class="brand"><span class="dot"></span><span class="name">Harrowgate Labs</span></div>
  <div class="col" style="left:17px;top:71px">
    <h3 class="h-dark">HEADING GOES HERE</h3>
    <p>Lorem ipsum dolor sit amet, consectetuer adipiscing elit, sed diam nonummy nibh euismod tincidunt ut laoreet dolore magna aliquam erat volutpat. Ut wisi enim ad minim veniam, quis nostrud exerci tation ullamcorper suscipit lobortis nisl ut aliquip ex ea tation ullamcorper suscipit lobortis nisl ut aliquip ex ea commodo consequat. Duis autem vel eum iriure dolor in hendrerit in vulputate velit esse molestie consequat, vel illum dolore eu feugiat nulla facilisis at vero eros et accumsan et iusto odio dignis Lorem ipsum dolor sit amet, consectetuer adipiscing elit, sed diam nonummy nibh euismod tincidunt ut laoreet dolore magna aliquam erat volutpat. Ut wisi enim ad minim veniam, quis nostrud exerci tation ullamcorper suscipit lobortis nisl ut aliquip ex ea tation ullamcorper suscipit lobortis nisl ut aliquip ex ea commodo consequat. Duis autem vel eum iriure dolor in hendrerit in vulputate velit esse molestie consequat, vel illum dolore eu feugiat nulla facilisis at vero eros et accumsan</p>
  </div>
  <div class="photo" role="img" aria-label="Photograph of colleagues smiling in a team meeting" style="left:17px;top:241px;width:127px;height:86px;border:1px solid #b9a983;background:linear-gradient(135deg,#8e9aa3,#d8dde0 60%,#b7bfc4)"></div>
  <div class="col" style="left:17px;top:331px">
    <p>Lorem ipsum dolor sit amet, consectetuer adipiscing elit, sed diam nonummy nibh euismod tincidunt ut laoreet dolore magna aliquam erat volutpat. Ut wisi enim ad minim veniam, quis nostrud exerci tation ullamcorper suscipit lobortis nisl ut aliquip ex ea commodo consequat. Duis autem vel eum iriure dolor in hendrerit in vulputate velit esse molestie</p>
  </div>
  <div class="col" style="left:167px;top:71px">
    <h3 class="h-dark">HEADING GOES HERE</h3>
    <p>Lorem ipsum dolor sit amet, consectetuer adipiscing elit, sed diam nonummy nibh euismod tincidunt ut laoreet dolore magna aliquam erat volutpat. Ut wisi enim ad minim veniam, quis nostrud exerci tation ullamcorper suscipit lobortis nisl ut aliquip ex ea tation ullamcorper suscipit lobortis nisl ut aliquip ex ea commodo consequat. Duis autem vel eum iriure dolor in hendrerit in vulputate velit esse molestie consequat, vel illum dolore eu feugiat nulla facilisis at vero eros et accumsan et iusto odio dignis Lorem ipsum dolor sit amet, consectetuer adipiscing elit, sed diam nonummy nibh euismod tincidunt ut laoreet dolore magna aliquam erat volutpat. Ut wisi enim ad minim veniam, quis nostrud exerci tation ullamcorper suscipit lobortis nisl ut aliquip ex ea tation ullamcorper suscipit lobortis nisl ut aliquip ex ea commodo consequat. Duis autem vel eum iriure dolor in hendrerit in vulputate velit esse molestie consequat, vel illum dolore eu feugiat nulla facilisis at vero eros et accumsan</p>
    <h3 class="h-dark" style="margin-top:9px">HEADING GOES HERE</h3>
    <p>Lorem ipsum dolor sit amet, consectetuer adipiscing elit, sed diam nonummy nibh euismod tincidunt ut laoreet dolore magna aliquam erat volutpat. Ut wisi enim ad minim veniam, quis nostrud exerci tation ullamcorper suscipit lobortis nisl ut aliquip ex ea tation ullamcorper suscipit lobortis nisl ut aliquip ex ea commodo consequat. Duis autem vel eum iriure dolor in hendrerit in vulputate velit esse molestie consequat, vel illum dolore eu feugiat nulla facilisis at vero eros et accumsan et iusto odio dignis Lorem ipsum dolor sit amet, consectetuer adipiscing elit, sed diam nonummy nibh euismod tincidunt ut laoreet dolore magna aliquam erat volutpat. Ut wisi enim ad minim veniam, quis nostrud exerci tation ullamcorper suscipit lobortis nisl ut aliquip ex ea tation ullamcorper suscipit lobortis nisl ut aliquip ex</p>
  </div>
  <footer class="footer"><span>FACILITIES MANAGEMENT SERVICE</span><span>COMPANY PROPOSAL 2024</span></footer>
</section>

<!-- Single-column page with image strip -->
<section class="page p6">
  <div class="top-band"></div>
  <h2 class="page-title"><span class="line1">HEADING</span><span class="line2">GOES HERE</span></h2>
  <div class="brand"><span class="dot"></span><span class="name">Harrowgate Labs</span></div>
  <div class="body" style="top:71px">
    <h3 class="h-dark">HEADING GOES HERE</h3>
    <p>Lorem ipsum dolor sit amet, consectetuer adipiscing elit, sed diam nonummy nibh euismod tincidunt ut laoreet dolore magna aliquam erat volutpat. Ut wisi enim ad minim veniam, quis nostrud exerci tation ullamcorper suscipit lobortis nisl ut aliquip ex ea tation ullamcorper suscipit lobortis nisl ut aliquip ex ea commodo consequat. Duis autem vel eum iriure dolor in hendrerit in vulputate velit esse molestie consequat, vel illum dolore eu feugiat nulla facilisis at vero eros et accumsan et iusto odio dignis Lorem ipsum dolor sit amet, consectetuer adipiscing elit, sed diam nonummy nibh euismod tincidunt ut laoreet dolore magna aliquam erat volutpat. Ut wisi enim ad minim veniam, quis nostrud exerci tation ullamcorper suscipit lobortis nisl ut aliquip ex ea tation ullamcorper suscipit lobortis nisl ut aliquip ex ea commodo consequat. Duis autem vel eum iriure dolor in hendrerit in vulputate velit esse molestie consequat, vel illum dolore eu feugiat nulla facilisis at vero eros et accumsan et iusto odio dignis</p>
    <h3 class="h-dark" style="margin-top:9px">HEADING GOES HERE</h3>
    <p>Lorem ipsum dolor sit amet, consectetuer adipiscing elit, sed diam nonummy nibh euismod tincidunt ut laoreet dolore magna aliquam erat volutpat. Ut wisi enim ad minim veniam, quis nostrud exerci tation ullamcorper suscipit lobortis nisl ut aliquip ex ea tation ullamcorper suscipit lobortis nisl ut aliquip ex ea commodo consequat. Duis autem vel eum iriure dolor in hendrerit in vulputate velit esse molestie consequat, vel illum dolore eu feugiat nulla facilisis at vero eros et accumsan et iusto odio dignis Lorem ipsum dolor sit amet,</p>
    <h3 class="h-dark" style="margin-top:9px">HEADING GOES HERE</h3>
    <p>Lorem ipsum dolor sit amet, consectetuer adipiscing elit, sed diam nonummy nibh euismod tincidunt ut laoreet dolore magna aliquam erat volutpat. Ut wisi enim ad minim veniam, quis nostrud exerci tation ullamcorper suscipit lobortis nisl ut aliquip ex ea tation ullamcorper suscipit lobortis nisl ut aliquip ex ea commodo consequat. Duis autem vel eum iriure dolor in hendrerit in vulputate velit esse molestie consequat, vel illum dolore eu feugiat nulla facilisis at vero eros et accumsan et iusto odio dignis Lorem ipsum dolor sit amet,</p>
  </div>
  <div class="photo" role="img" aria-label="Strip of four photographs of industrial plants and laboratory equipment" style="left:18px;top:284px;width:278px;height:67px;background:linear-gradient(90deg,#6f8fa3 0%,#9aa7ae 25%,#a07a5c 30%,#c9a98d 45%,#2f6f8f 52%,#5fa0bf 68%,#cdd9e3 76%,#9fb7cc 100%)"></div>
  <footer class="footer"><span>FACILITIES MANAGEMENT SERVICE</span><span>COMPANY PROPOSAL 2024</span></footer>
</section>

</body>
</html>
```